Harbor Ridge Painting Epoxy Flyer

We need a promotional flyer for a new epoxy floor coatings division of our painting company. We do epoxy garage floor coatings and paver sealing. It needs to be based on and very similar to the attached flyer. The garage floor picture needs to look more realistic, and the before and after pavers pictures should look less shiny but still a good contrast. Include attached logo

```html
<!DOCTYPE html>
<html lang="en">
<head>
<meta charset="utf-8">
<title>Harbor Ridge Painting Epoxy Flyer</title>
<link href="https://fonts.googleapis.com/css2?family=Poppins:ital,wght@0,300;0,400;0,500;0,600;0,700;0,800;1,300;1,600;1,700;1,800&display=swap" rel="stylesheet">
<style>
:root{
  --sage:#6f8b79;
  --amber:#c9792a;
  --paper:#ffffff;
  --ink:#5b5b5b;
  --mist:#e6e6e6;
  --stage:#5a5a5a;
  --concrete-a:#8c8b86;
  --concrete-b:#4b4b48;
  --paver-a:#8e6d55;
  --paver-b:#5a4837;
  --epoxy-a:#b8bab8;
  --epoxy-b:#555858;
  --sealed-a:#9a5f3a;
  --sealed-b:#4f3c2b;
}
*{margin:0;padding:0;box-sizing:border-box}
html,body{width:1200px;height:706px;overflow:hidden;background:var(--stage);font-family:'Poppins',sans-serif}
.stage{position:relative;width:1200px;height:706px}
.flyer{position:absolute;left:356px;top:8px;width:915px;height:1295px;background:var(--paper);transform:scale(.5328);transform-origin:0 0;overflow:hidden;box-shadow:0 6px 24px rgba(0,0,0,.35)}
.abs{position:absolute}
.top-band{left:0;top:0;width:915px;height:14px;background:var(--sage)}
.headline{left:0;top:28px;width:915px;text-align:center}
.headline .lead{display:block;font-weight:400;font-style:italic;color:var(--amber);font-size:66px;line-height:1;letter-spacing:1px;transform:translateX(-10px)}
.headline .main{display:block;font-weight:800;font-style:italic;color:var(--sage);font-size:80px;line-height:1.05;text-shadow:2px 4px 5px rgba(0,0,0,.25)}
.headline .amp{color:var(--amber)}
.dots{top:222px;width:98px;height:8px;background:radial-gradient(circle,var(--amber) 3px,transparent 3.5px) 0 0/16px 8px repeat-x}
.dots.left{left:42px}.dots.right{left:777px}
.tagline{left:178px;top:197px;width:562px;height:50px;background:var(--sage);clip-path:polygon(3% 0,100% 0,97% 100%,0 100%);color:#fff;font-weight:500;font-size:34px;line-height:50px;text-align:center}
.photo{display:flex;align-items:flex-end;justify-content:center;padding-bottom:10px;border-radius:10px;color:#fff;font-weight:700;font-size:30px;letter-spacing:.5px;text-shadow:0 2px 4px rgba(0,0,0,.6)}
.photo span{transform:translateX(-20px)}
.garage-before{left:42px;top:271px;width:428px;height:214px;background:linear-gradient(170deg,var(--concrete-a),var(--concrete-b));clip-path:polygon(0 0,100% 0,92% 100%,0 100%)}
.paver-before{left:446px;top:271px;width:427px;height:214px;background:linear-gradient(170deg,var(--paver-a),var(--paver-b));clip-path:polygon(6% 0,100% 0,100% 100%,0 100%)}
.garage-after{left:42px;top:501px;width:400px;height:215px;background:linear-gradient(170deg,var(--epoxy-a),var(--epoxy-b));clip-path:polygon(0 0,100% 0,96% 100%,0 100%)}
.paver-after{left:420px;top:501px;width:453px;height:215px;background:linear-gradient(170deg,var(--sealed-a),var(--sealed-b));clip-path:polygon(4% 0,100% 0,100% 100%,0 100%)}
.service-head{top:732px;height:58px;background:var(--amber);color:#fff;font-weight:700;font-size:27px;line-height:58px;padding-left:42px}
.service-head.epoxy{left:0;width:423px}
.service-head.paver{left:429px;width:486px;padding-left:39px}
.service-body{top:790px;height:185px;background:var(--sage)}
.service-body.epoxy{left:0;width:423px}
.service-body.paver{left:429px;width:486px}
.service-divider{left:423px;top:732px;width:6px;height:243px;background:var(--paper)}
.checks{list-style:none;padding:14px 0 0 42px}
.service-body.paver .checks{padding-left:39px}
.checks li{display:flex;align-items:center;gap:12px;color:#fff;font-size:19px;height:32px}
.checks svg{width:28px;height:24px;flex:none}
.promise{left:115px;top:952px;width:680px;height:44px;background:var(--amber);clip-path:polygon(3% 0,100% 0,97% 100%,0 100%);color:#fff;font-weight:600;font-style:italic;font-size:23px;line-height:44px;text-align:center}
.trust{top:1025px;display:flex;align-items:center;gap:16px;color:var(--ink);font-size:21px;line-height:1.15}
.trust svg{width:44px;height:48px;flex:none}
.trust.licensed{left:70px}.trust.family{left:312px}.trust.area{left:610px}
.brand{left:42px;top:1110px;width:190px;height:150px;display:flex;flex-direction:column;align-items:center;justify-content:center;gap:12px;text-align:center}
.brand .dot{width:46px;height:46px;border-radius:50%;background:var(--sage)}
.brand .name{font-weight:600;font-size:20px;line-height:1.2;color:var(--sage)}
.estimate{left:370px;top:1106px;width:435px;height:60px;border:3px solid var(--amber);border-bottom:none;border-radius:10px 10px 0 0;transform:skewX(-6deg);color:var(--sage);font-weight:700;font-size:28px;line-height:56px;text-align:center}
.estimate span{display:inline-block;transform:skewX(6deg)}
.contact-bar{left:240px;top:1165px;width:675px;height:103px;background:var(--mist);border-radius:24px 0 0 24px}
.phone{left:286px;top:1180px;display:flex;align-items:center;gap:12px;color:var(--sage);font-weight:700;font-size:40px;line-height:1}
.phone svg{width:28px;height:28px}
.web{left:290px;top:1228px;display:flex;align-items:center;gap:14px;color:var(--ink);font-size:20px}
.web svg{width:22px;height:22px}
.pledge{left:665px;top:1172px;width:250px;height:90px;background:var(--amber);border-radius:10px 0 0 10px;color:#fff;font-weight:700;font-size:19px;line-height:1.12;padding:22px 0 0 20px}
</style>
</head>
<body>
<div class="stage">
  <div class="flyer">
    <div class="abs top-band"></div>

    <h1 class="abs headline">
      <span class="lead">Upgrade Your</span>
      <span class="main">Garage <span class="amp">&amp;</span> Driveway</span>
    </h1>

    <div class="abs dots left"></div>
    <div class="abs dots right"></div>
    <div class="abs tagline">From worn-out to like new</div>

    <div class="abs photo garage-before" role="img" aria-label="Photo: worn, stained concrete garage floor before coating"><span>BEFORE</span></div>
    <div class="abs photo paver-before" role="img" aria-label="Photo: faded, weathered paver patio before sealing"><span>BEFORE</span></div>
    <div class="abs photo garage-after" role="img" aria-label="Photo: garage floor with grey flake epoxy coating after"><span>AFTER</span></div>
    <div class="abs photo paver-after" role="img" aria-label="Photo: sealed paver patio with restored warm color after"><span>AFTER</span></div>

    <div class="abs service-head epoxy">EPOXY FLOOR COATINGS</div>
    <div class="abs service-head paver">PAVER SEALING</div>
    <div class="abs service-divider"></div>

    <div class="abs service-body epoxy">
      <ul class="checks">
        <li><svg viewBox="0 0 28 24"><rect x="1.5" y="3.5" width="19" height="19" rx="3" fill="none" stroke="#fff" stroke-width="2.5"/><path d="M6 12l5 5L26 2" fill="none" stroke="#fff" stroke-width="3.5" stroke-linecap="round" stroke-linejoin="round"/></svg>Durable, long-lasting finish</li>
        <li><svg viewBox="0 0 28 24"><rect x="1.5" y="3.5" width="19" height="19" rx="3" fill="none" stroke="#fff" stroke-width="2.5"/><path d="M6 12l5 5L26 2" fill="none" stroke="#fff" stroke-width="3.5" stroke-linecap="round" stroke-linejoin="round"/></svg>Slip-resistant texture</li>
        <li><svg viewBox="0 0 28 24"><rect x="1.5" y="3.5" width="19" height="19" rx="3" fill="none" stroke="#fff" stroke-width="2.5"/><path d="M6 12l5 5L26 2" fill="none" stroke="#fff" stroke-width="3.5" stroke-linecap="round" stroke-linejoin="round"/></svg>Covers cracks &amp; imperfections</li>
        <li><svg viewBox="0 0 28 24"><rect x="1.5" y="3.5" width="19" height="19" rx="3" fill="none" stroke="#fff" stroke-width="2.5"/><path d="M6 12l5 5L26 2" fill="none" stroke="#fff" stroke-width="3.5" stroke-linecap="round" stroke-linejoin="round"/></svg>Easy to clean &amp; maintain</li>
      </ul>
    </div>
    <div class="abs service-body paver">
      <ul class="checks">
        <li><svg viewBox="0 0 28 24"><rect x="1.5" y="3.5" width="19" height="19" rx="3" fill="none" stroke="#fff" stroke-width="2.5"/><path d="M6 12l5 5L26 2" fill="none" stroke="#fff" stroke-width="3.5" stroke-linecap="round" stroke-linejoin="round"/></svg>Restores color &amp; enhances appearance</li>
        <li><svg viewBox="0 0 28 24"><rect x="1.5" y="3.5" width="19" height="19" rx="3" fill="none" stroke="#fff" stroke-width="2.5"/><path d="M6 12l5 5L26 2" fill="none" stroke="#fff" stroke-width="3.5" stroke-linecap="round" stroke-linejoin="round"/></svg>Protects from sun fading</li>
        <li><svg viewBox="0 0 28 24"><rect x="1.5" y="3.5" width="19" height="19" rx="3" fill="none" stroke="#fff" stroke-width="2.5"/><path d="M6 12l5 5L26 2" fill="none" stroke="#fff" stroke-width="3.5" stroke-linecap="round" stroke-linejoin="round"/></svg>Helps prevent weeds &amp; sand loss</li>
        <li><svg viewBox="0 0 28 24"><rect x="1.5" y="3.5" width="19" height="19" rx="3" fill="none" stroke="#fff" stroke-width="2.5"/><path d="M6 12l5 5L26 2" fill="none" stroke="#fff" stroke-width="3.5" stroke-linecap="round" stroke-linejoin="round"/></svg>Easier to clean &amp; maintain</li>
      </ul>
    </div>

    <div class="abs promise">Practical upgrades that protect and improve your home</div>

    <div class="abs trust licensed">
      <svg viewBox="0 0 44 48"><path d="M22 3l17 6v12c0 12-8 20-17 24C13 41 5 33 5 21V9z" fill="var(--amber)"/><rect x="14" y="14" width="14" height="18" rx="2" fill="#fff"/><circle cx="31" cy="31" r="6" fill="#fff" stroke="var(--amber)" stroke-width="2"/></svg>
      <span>Licensed &amp;<br>Insured</span>
    </div>
    <div class="abs trust family">
      <svg viewBox="0 0 44 48"><path d="M22 30C10 22 6 16 6 11a8 8 0 0 1 16-2 8 8 0 0 1 16 2c0 5-4 11-16 19z" fill="var(--amber)"/><circle cx="8" cy="38" r="3.5" fill="var(--amber)"/><circle cx="22" cy="40" r="3.5" fill="var(--amber)"/><circle cx="36" cy="38" r="3.5" fill="var(--amber)"/></svg>
      <span>Family-Owned<br>Local Business</span>
    </div>
    <div class="abs trust area">
      <svg viewBox="0 0 44 48"><path d="M22 3a12 12 0 0 0-12 12c0 9 12 20 12 20s12-11 12-20A12 12 0 0 0 22 3z" fill="var(--amber)"/><circle cx="22" cy="15" r="5" fill="#fff"/><path d="M4 44l10-8 8 6 8-6 10 8" fill="none" stroke="var(--amber)" stroke-width="3"/></svg>
      <span>Serving Cedar Valley &amp;<br>Surrounding Areas</span>
    </div>

    <div class="abs brand">
      <div class="dot"></div>
      <div class="name">Harbor Ridge Painting</div>
    </div>

    <div class="abs estimate"><span>CALL FOR A FREE ESTIMATE</span></div>
    <div class="abs contact-bar"></div>
    <div class="abs phone">
      <svg viewBox="0 0 24 24"><path d="M6.6 10.8a15 15 0 0 0 6.6 6.6l2.2-2.2a1 1 0 0 1 1-.25 11.4 11.4 0 0 0 3.6.57 1 1 0 0 1 1 1V20a1 1 0 0 1-1 1A17 17 0 0 1 3 4a1 1 0 0 1 1-1h3.5a1 1 0 0 1 1 1c0 1.25.2 2.45.57 3.6a1 1 0 0 1-.25 1z" fill="var(--amber)"/></svg>
      <span>555-014-2290</span>
    </div>
    <div class="abs web">
      <svg viewBox="0 0 24 24"><circle cx="12" cy="12" r="10" fill="none" stroke="var(--amber)" stroke-width="2"/><path d="M2 12h20M12 2c3 3 3 17 0 20M12 2c-3 3-3 17 0 20" fill="none" stroke="var(--amber)" stroke-width="2"/></svg>
      <span>www.harborridgepainting.com</span>
    </div>
    <div class="abs pledge">Fast, professional<br>service you can trust</div>
  </div>
</div>
</body>
</html>
```